Buch-/eBook-Cover für Geschichte zum Pride auf Gran Canaria
Zielgruppe
Zielgruppe: Reisefreudige junge schwule Männer
Aufgabenstellung
Die Geschichte spielt zum Pride auf Gran Canaria. Es geht um vier Freunde die dort ihre Ferien verbingen.
Ich stelle mir vor, dass auf dem Cover die Regenbogenflagge ist, Strand, Meer, keine Menschen und ein fetter Schriftzug mit dem Titel #TorvilenaGlanz. Daneben sollte kleiner mein Name Ferdinand zu Brakwede stehen. Das Cover kann aber auch gern wie ein Partyflyer designt sein und der Titel wie ein Logo wirken.
Bin aber für alternativen offen.

```html
<!DOCTYPE html>
<html lang="de">
<head>
<meta charset="utf-8">
<title>#TorvilenaGlanz – Ferdinand zu Brakwede</title>
<link rel="stylesheet" href="https://fonts.googleapis.com/css2?family=Alfa+Slab+One&family=Montserrat:wght@800&display=swap">
<style>
  :root {
    --stage: #a8a8a8;
    --sky-teal: #7fd3dc;
    --sky-pink: #f4a7a8;
    --glow: #fff6ee;
    --sea: #5cc6cf;
    --foam: #f7ecf0;
    --sand: #d98a6a;
    --sand-deep: #c8735a;
    --rb-red: #e8174f;
    --rb-magenta: #e0288c;
    --rb-purple: #8a5cd4;
    --rb-blue: #36b6e8;
    --rb-green: #92cf3e;
    --star: #ffe01a;
    --white: #ffffff;
  }
  html, body {
    margin: 0;
    width: 1200px;
    height: 2317px;
    overflow: hidden;
    background: var(--stage);
  }
  .book-cover {
    position: absolute;
    left: 50px;
    top: 326px;
    width: 1100px;
    height: 1665px;
    overflow: hidden;
    box-shadow: 0 14px 40px rgba(0,0,0,0.35);
  }
  .cover-scene {
    position: absolute;
    inset: 0;
    background:
      radial-gradient(ellipse 55% 22% at 50% 58%, rgba(255,255,255,0.95), rgba(255,255,255,0) 70%),
      radial-gradient(ellipse 60% 30% at 80% 20%, rgba(244,160,170,0.8), rgba(244,160,170,0) 70%),
      linear-gradient(180deg,
        var(--sky-teal) 0%,
        #a6dfe3 18%,
        var(--sky-pink) 34%,
        var(--glow) 50%,
        var(--sea) 60%,
        var(--foam) 70%,
        #e7a98c 78%,
        var(--sand) 88%,
        var(--sand-deep) 100%);
  }
  .balloon-art {
    position: absolute;
    left: 382px;
    top: 143px;
    width: 334px;
    height: 400px;
    border-radius: 50% 50% 42% 42% / 56% 56% 44% 44%;
    background: linear-gradient(90deg, var(--rb-green), #f2e23a 30%, var(--rb-blue) 55%, var(--rb-purple) 80%, #6b3fb0);
    opacity: 0.9;
  }
  .title-art {
    position: absolute;
    inset: 0;
    width: 1100px;
    height: 1665px;
  }
  .title-line {
    font-family: "Alfa Slab One", serif;
    fill: var(--white);
    stroke: url(#rainbow);
    stroke-linejoin: round;
    paint-order: stroke;
  }
  .title-shadow {
    font-family: "Alfa Slab One", serif;
    fill: rgba(120,60,150,0.35);
  }
  .author-name {
    font-family: "Montserrat", sans-serif;
    font-weight: 800;
    font-size: 40px;
    fill: var(--white);
    letter-spacing: 1px;
  }
  .ribbon-star { fill: var(--star); }
</style>
</head>
<body>
  <div class="book-cover">
    <div class="cover-scene" role="img" aria-label="Sonnenuntergang am Strand mit Meer, Wellen, rosa Wolken und Glitzer"></div>
    <div class="balloon-art" role="img" aria-label="Heißluftballon in Regenbogenfarben"></div>

    <svg class="title-art" viewBox="0 0 1100 1665" xmlns="http://www.w3.org/2000/svg">
      <defs>
        <linearGradient id="rainbow" x1="0" y1="0" x2="1" y2="0">
          <stop offset="0" stop-color="var(--rb-red)"/>
          <stop offset="0.25" stop-color="var(--rb-magenta)"/>
          <stop offset="0.5" stop-color="var(--rb-purple)"/>
          <stop offset="0.75" stop-color="var(--rb-blue)"/>
          <stop offset="1" stop-color="var(--rb-green)"/>
        </linearGradient>
        <path id="ribbon-mid" d="M150,1060 Q555,1165 960,1060"/>
      </defs>

      <text class="title-shadow" x="88" y="672" font-size="132" textLength="947" lengthAdjust="spacingAndGlyphs">#TORVILENA</text>
      <text class="title-line" x="78" y="662" font-size="132" stroke-width="24" textLength="947" lengthAdjust="spacingAndGlyphs">#TORVILENA</text>

      <text class="title-shadow" x="82" y="1012" font-size="310" textLength="950" lengthAdjust="spacingAndGlyphs">GLANZ</text>
      <text class="title-line" x="72" y="1000" font-size="310" stroke-width="30" textLength="950" lengthAdjust="spacingAndGlyphs">GLANZ</text>

      <path class="author-ribbon" fill="url(#rainbow)"
            d="M100,1020 Q555,1120 1010,1010 L1012,1090 Q555,1215 98,1100 Z"/>
      <text class="author-name">
        <textPath href="#ribbon-mid" startOffset="50%" text-anchor="middle">FERDINAND ZU BRAKWEDE</textPath>
      </text>
      <polygon class="ribbon-star" points="135,1045 142,1060 158,1062 146,1073 149,1089 135,1081 121,1089 124,1073 112,1062 128,1060"/>
      <polygon class="ribbon-star" points="975,1040 982,1055 998,1057 986,1068 989,1084 975,1076 961,1084 964,1068 952,1057 968,1055"/>
    </svg>
  </div>
</body>
</html>
```